Oriel Photography Business Card

I need a business card designed for a photography business based in Perth, Western Australia called Oriel Photography.

We specialise in wedding, event photography and portrait photography.

The business card must borrow the style of the attached logo.

The hex codes for the colours in the logo are:
#ED1D85 - Pink
#89C23E - Green
#37282F - Black

The name on the card will be:
Name: Tobrian
Phone: 0417395268
Website: www.orielphotography.example.com.au
Facebook: orielphotography

I am open and happy to accept creative concepts.

I’d like some space at the back for writing notes and appointment details.

```html
<!DOCTYPE html>
<html lang="en">
<head>
<meta charset="utf-8">
<title>Oriel Photography – Business Card</title>
<link rel="stylesheet" href="https://fonts.googleapis.com/css2?family=Josefin+Sans:wght@300&family=Give+You+Glory&family=Cutive+Mono&display=swap">
<style>
  :root {
    --pink: #ED1D85;
    --green: #89C23E;
    --ink: #37282F;
    --paper: #ffffff;
    --backdrop: #cde0cf;
    --mist: #e6e6e6;
    --card-w: 504px;
    --card-h: 288px;
  }
  * { box-sizing: border-box; margin: 0; padding: 0; }
  html, body { width: 1200px; height: 848px; overflow: hidden; }
  body {
    background: var(--backdrop);
    display: flex;
    align-items: center;
    justify-content: center;
    gap: 60px;
  }
  .card {
    position: relative;
    width: var(--card-w);
    height: var(--card-h);
    background: var(--paper);
    overflow: hidden;
    box-shadow: 0 6px 18px rgba(55, 40, 47, 0.18);
  }

  /* Front */
  .card-front__band {
    position: absolute;
    inset: 0 auto 0 0;
    width: 40%;
  }
  .card-front__band svg { display: block; width: 100%; height: 100%; }
  .card-front__tagline {
    position: absolute;
    left: 22px;
    top: 112px;
    font-family: 'Josefin Sans', sans-serif;
    font-weight: 300;
    font-size: 15px;
    letter-spacing: 0.45em;
    color: var(--paper);
  }
  .card-front__sheen {
    position: absolute;
    right: 0;
    bottom: 0;
    width: 60%;
    height: 100%;
  }
  .card-front__sheen svg { display: block; width: 100%; height: 100%; }
  .brand {
    position: absolute;
    left: 40%;
    right: 0;
    top: 48px;
    display: flex;
    flex-direction: column;
    align-items: center;
    gap: 18px;
  }
  .brand__dot {
    width: 58px;
    height: 58px;
    border-radius: 50%;
    background: var(--pink);
  }
  .brand__name {
    font-family: 'Josefin Sans', sans-serif;
    font-weight: 300;
    font-size: 14px;
    letter-spacing: 0.4em;
    text-transform: uppercase;
    color: var(--ink);
    text-align: center;
    line-height: 1.5;
  }

  /* Back */
  .card-back { border: 6px solid var(--pink); }
  .contact {
    position: absolute;
    right: 36px;
    top: 44px;
    display: flex;
    flex-direction: column;
    align-items: flex-start;
    gap: 8px;
    color: var(--ink);
  }
  .contact__name {
    font-family: 'Give You Glory', cursive;
    font-size: 44px;
    line-height: 1.1;
    margin-bottom: 6px;
  }
  .contact__line {
    display: flex;
    align-items: center;
    gap: 10px;
    font-family: 'Cutive Mono', monospace;
    font-size: 15px;
  }
  .contact__line--phone {
    font-family: 'Give You Glory', cursive;
    font-size: 26px;
  }
  .contact__icon { width: 16px; height: 16px; flex: none; }
  .contact__square {
    width: 13px;
    height: 13px;
    background: var(--ink);
    flex: none;
  }
  .contact__web {
    font-family: 'Cutive Mono', monospace;
    font-size: 13px;
  }
  .notes-space {
    position: absolute;
    left: 36px;
    bottom: 36px;
    width: 120px;
    height: 60px;
  }
</style>
</head>
<body>

  <section class="card card-front" aria-label="Business card front">
    <div class="card-front__band">
      <svg viewBox="0 0 200 288" preserveAspectRatio="none" aria-hidden="true">
        <defs>
          <linearGradient id="band-gloss" x1="0" y1="0" x2="1" y2="1">
            <stop offset="0" stop-color="#ffffff" stop-opacity="0.55"/>
            <stop offset="0.35" stop-color="#ffffff" stop-opacity="0"/>
          </linearGradient>
        </defs>
        <rect width="200" height="288" fill="var(--pink)"/>
        <rect width="200" height="288" fill="url(#band-gloss)"/>
        <polygon points="0,190 200,190 200,288 70,288" fill="var(--ink)"/>
      </svg>
    </div>
    <p class="card-front__tagline">PHOTOGRAPHY</p>
    <div class="card-front__sheen">
      <svg viewBox="0 0 300 288" preserveAspectRatio="none" aria-hidden="true">
        <defs>
          <linearGradient id="paper-sheen" x1="0" y1="1" x2="1" y2="0">
            <stop offset="0" stop-color="var(--mist)"/>
            <stop offset="1" stop-color="#ffffff" stop-opacity="0"/>
          </linearGradient>
        </defs>
        <polygon points="0,190 300,110 300,288 0,288" fill="url(#paper-sheen)"/>
      </svg>
    </div>
    <div class="brand">
      <span class="brand__dot" aria-hidden="true"></span>
      <p class="brand__name">Oriel Photography</p>
    </div>
  </section>

  <section class="card card-back" aria-label="Business card back">
    <div class="notes-space" aria-hidden="true"></div>
    <div class="contact">
      <p class="contact__name">Tobrian</p>
      <p class="contact__line contact__line--phone">
        <svg class="contact__icon" viewBox="0 0 24 24" aria-hidden="true">
          <path d="M6.6 10.8a15 15 0 0 0 6.6 6.6l2.2-2.2a1 1 0 0 1 1-.25 11.4 11.4 0 0 0 3.6.57 1 1 0 0 1 1 1V20a1 1 0 0 1-1 1A17 17 0 0 1 3 4a1 1 0 0 1 1-1h3.5a1 1 0 0 1 1 1c0 1.25.2 2.45.57 3.57a1 1 0 0 1-.25 1z" fill="var(--ink)"/>
        </svg>
        0417395268
      </p>
      <p class="contact__line">
        <span class="contact__square" aria-hidden="true"></span>
        orielphotography
      </p>
      <p class="contact__web">www.orielphotography.example.com.au</p>
    </div>
  </section>

</body>
</html>
```